Business Card Design - Photographer

I am a landscape photographer and I require a business card design. 

I require two designs:
1)  a double sided business card
 and
b)  a single sided business card 

The single sided design can either be the same as the double sided (with just one side having all the information)....or it can be an entire new design. Its up to you.

My corporate colours are (CMYK):

Blue   69, 32, 0, 0
Grey  72,  64,  47,  31
Green  32,  2,  91,  0
Yellow   0, 19, 92, 0
Orange  0, 39, 75, 0

Colour space in final file should be in CMYK.

The details that need to be included on the card:

- Use the provided Logo
- Name: Wiktor Baranowski
- Email:   sales@vistalumeworks.com.au
- Website:    vistalumeworks.com.au
- Twitter:    twitter.com/vistalumeworks
- Facebook:   facebook.com/vistalumeworks
- Mobile  0417 539 662

Please use the attached template to design the logo to the specified size, including the marked bleed lines. I have also attached my logo in PNG (transparent background) and ai format for you to use.

The final file should be:
- Photoshop version with layers so I can edit the name/text etc. All non vector files should be high resolution at 1039 x 697 pixels at 300 dpi.

I also require a file as:
- Vector based PDF

Anyway questions please contact me.

Thank you

Industry/Entity Type

Landscape

Logo styles of interest
Pictorial/Combination Logo
Abstract Logo
Wordmark Logo
Lettermark Logo
Requirements
Must have
• The details that need to be included on the card:

- Use the provided Logo
- Name: Wiktor Baranowski
- Email: sales@vistalumeworks.com.au
- Website: vistalumeworks.com.au
- Twitter: twitter.com/vistalumeworks
- Facebook: facebook.com/vistalumeworks
- Mobile 0417 539 662

```html
<!DOCTYPE html>
<html lang="en">
<head>
<meta charset="utf-8">
<title>Vistalume Works – Business Cards</title>
<link rel="stylesheet" href="https://fonts.googleapis.com/css2?family=Cinzel:wght@500&family=Mulish:wght@400;700&display=swap">
<style>
  :root {
    --backdrop: #a9a9a9;
    --card-dark: #4a4658;
    --card-light: #ecebe8;
    --ink-dark: #44404f;
    --ink-light: #ffffff;
    --rule-dark: #8d8a95;
    --rule-light: #ffffff;
  }
  * { margin: 0; padding: 0; box-sizing: border-box; }
  html, body {
    width: 1200px;
    height: 900px;
    overflow: hidden;
    background: var(--backdrop);
  }
  .stage {
    position: relative;
    width: 1200px;
    height: 900px;
  }
  .card {
    position: absolute;
    top: 155px;
    width: 360px;
    height: 590px;
    box-shadow: 0 6px 18px rgba(0,0,0,0.25);
  }
  .card--front { left: 180px; background: var(--card-dark); }
  .card--back  { left: 660px; background: var(--card-light); }

  .brand {
    position: absolute;
    left: 0;
    right: 0;
    display: flex;
    flex-direction: column;
    align-items: center;
  }
  .brand__dot { border-radius: 50%; }
  .brand__name {
    font-family: "Cinzel", serif;
    font-weight: 500;
    white-space: nowrap;
    letter-spacing: 0.02em;
  }
  .brand__rule { height: 1px; }

  .card--front .brand { top: 150px; }
  .card--front .brand__dot { width: 62px; height: 62px; background: var(--ink-light); margin-bottom: 14px; }
  .card--front .brand__name { font-size: 29px; color: var(--ink-light); }
  .card--front .brand__rule { width: 300px; background: var(--rule-light); margin-top: 6px; }

  .card--back .brand { top: 60px; }
  .card--back .brand__dot { width: 44px; height: 44px; background: var(--ink-dark); margin-bottom: 10px; }
  .card--back .brand__name { font-size: 21px; color: var(--ink-dark); }
  .card--back .brand__rule { width: 240px; background: var(--ink-dark); margin-top: 5px; }

  .holder {
    position: absolute;
    top: 185px;
    left: 0;
    right: 0;
    text-align: center;
    font-family: "Mulish", sans-serif;
    font-weight: 400;
    font-size: 26px;
    color: var(--ink-dark);
  }
  .contact {
    position: absolute;
    top: 268px;
    left: 36px;
    right: 36px;
    list-style: none;
    font-family: "Mulish", sans-serif;
    font-size: 15px;
    color: var(--ink-dark);
  }
  .contact__item {
    padding: 9px 0 8px;
    border-bottom: 1px solid var(--rule-dark);
    white-space: nowrap;
  }
  .contact__item:last-child { border-bottom: none; }
  .contact__item--phone { text-align: center; border-bottom: none; padding-bottom: 2px; }
  .contact__item--web { font-weight: 700; font-size: 16px; }
</style>
</head>
<body>
<main class="stage">
  <section class="card card--front" aria-label="Card front">
    <div class="brand">
      <span class="brand__dot"></span>
      <span class="brand__name">VISTALUME WORKS</span>
      <span class="brand__rule"></span>
    </div>
  </section>

  <section class="card card--back" aria-label="Card back">
    <div class="brand">
      <span class="brand__dot"></span>
      <span class="brand__name">VISTALUME WORKS</span>
      <span class="brand__rule"></span>
    </div>
    <p class="holder">Wiktor Baranowski</p>
    <ul class="contact">
      <li class="contact__item contact__item--phone">M: 0417 539 662</li>
      <li class="contact__item">E:&nbsp; sales@vistalumeworks.com.au</li>
      <li class="contact__item">chirpline.com/vistalumeworks</li>
      <li class="contact__item">friendhub.com/vistalumeworks</li>
      <li class="contact__item contact__item--web">vistalumeworks.com.au</li>
    </ul>
  </section>
</main>
</body>
</html>
```